Tidewell Deli Deli offering takeaway products in various packaging formats

We need a range of modern, clean, standout colourful designs that can be used on multiple packaging for a range of takeaway packaging. The use of multi coloured fish scales in the design or seafood related design element is preferential. Modern, creative, vibrant, fun, clean please.
Each design that may be used on each individual packaging must identify itself as been part of a corporate brand.

Target Market(s)

Modern, upmarket foodie

Font styles to use
Serif

Colors
fbed26
33a6d7
85cae6
acd036
f04a50
eea4c8
b7a5cd
0455a3

Requirements
Must have
• Colour, vibrancy, seafood connection, creativity, clean design,
Nice to have
• creativity
Should not have
• Old fashioned, generic images, poor images

```html
<!DOCTYPE html>
<html lang="en">
<head>
<meta charset="utf-8">
<title>Tidewell Deli – Packaging Cover Range</title>
<link rel="stylesheet" href="https://fonts.googleapis.com/css2?family=Montserrat:wght@500&display=swap">
<style>
  :root {
    --bg-graphite: #5f5f5f;
    --bg-slate: #56707d;
    --bg-mauve: #8a7480;
    --cover-black: #242424;
    --cover-sky: #93d2e6;
    --cover-pink: #eaafd1;
    --label-white: #ffffff;
    --ink-navy: #2a55a8;
    --ink-sky: #33a6d7;
    --scale-blue: #33a6d7;
    --scale-light: #85cae6;
    --scale-green: #acd036;
    --scale-red: #f04a50;
    --scale-pink: #eea4c8;
    --scale-navy: #0455a3;
  }
  * { margin: 0; padding: 0; box-sizing: border-box; }
  html, body { width: 1200px; height: 3325px; overflow: hidden; }
  body { font-family: "Montserrat", sans-serif; }

  .panel {
    height: 1108.33px;
    display: flex;
    align-items: center;
    justify-content: center;
  }
  .panel--graphite { background: var(--bg-graphite); }
  .panel--slate { background: var(--bg-slate); }
  .panel--mauve { background: var(--bg-mauve); }

  .cover {
    position: relative;
    width: 640px;
    height: 640px;
    box-shadow: 0 24px 50px rgba(0,0,0,.3);
  }
  .cover--black { background: var(--cover-black); --accent: #3f8fd9; --accent-light: #9fc8ef; --name-ink: var(--ink-navy); }
  .cover--sky { background: var(--cover-sky); --accent: #44afd6; --accent-light: #bfe4f2; --name-ink: var(--ink-sky); }
  .cover--pink { background: var(--cover-pink); --accent: #2463b5; --accent-light: #c9d8ee; --name-ink: var(--ink-navy); }

  .scale-band {
    position: absolute;
    left: 300px;
    top: 0;
    width: 270px;
    height: 340px;
    background: linear-gradient(160deg,
      var(--scale-navy) 0%, var(--scale-blue) 22%, var(--scale-pink) 42%,
      var(--scale-green) 60%, var(--scale-red) 78%, var(--scale-light) 100%);
  }

  .brand-label {
    position: absolute;
    left: 312px;
    top: 310px;
    width: 300px;
    height: 150px;
    background: var(--label-white);
    display: flex;
    align-items: center;
    justify-content: center;
  }
  .brand-label__name {
    font-family: "Montserrat", sans-serif;
    font-weight: 500;
    font-size: 30px;
    letter-spacing: .04em;
    color: var(--name-ink);
    white-space: nowrap;
  }

  .accent-bar {
    position: absolute;
    left: 60px;
    top: 370px;
    width: 200px;
    height: 82px;
    background: linear-gradient(120deg,
      var(--accent) 0%, var(--accent) 35%, var(--accent-light) 62%,
      var(--accent) 62.5%, var(--accent) 100%);
  }
</style>
</head>
<body>
  <section class="panel panel--graphite">
    <div class="cover cover--black">
      <div class="scale-band" role="img" aria-label="Multicoloured fish scale pattern"></div>
      <div class="brand-label"><span class="brand-label__name">Tidewell Deli</span></div>
      <div class="accent-bar"></div>
    </div>
  </section>

  <section class="panel panel--slate">
    <div class="cover cover--sky">
      <div class="scale-band" role="img" aria-label="Multicoloured fish scale pattern"></div>
      <div class="brand-label"><span class="brand-label__name">Tidewell Deli</span></div>
      <div class="accent-bar"></div>
    </div>
  </section>

  <section class="panel panel--mauve">
    <div class="cover cover--pink">
      <div class="scale-band" role="img" aria-label="Multicoloured fish scale pattern"></div>
      <div class="brand-label"><span class="brand-label__name">Tidewell Deli</span></div>
      <div class="accent-bar"></div>
    </div>
  </section>
</body>
</html>
```